Business Card Design

Lawyer
Business name "Harlow Law"
Areas of expertise:
property
commercial
trusts
immigration
franchising
I want the following quote on the back of the card somewhere.
"Education is when you read the fine print,
experience is what you get if you don't." Dirk Vanholm
Probably the "areas of expertise" should be on the back also to avoid cluttering the front.
As for colours, I like the shades of blue used on qvelbank.com.
The basic part of the card with the contact info needs to be white and uncluttered.
Target Market(s)
small to medium sized self employed business people
Industry/Entity Type
Business
Contact Information for Business Card
Glen Harlow
Phone + 64 9 514 6937
Fax: + 64 9 514 6936
PO Box 734
Kestrel Bay
Tarnhaven 3961
NZ
email: glen@fernmarklaw.co.nz

```html
<!DOCTYPE html>
<html lang="en">
<head>
<meta charset="utf-8">
<title>Harlow Law Business Card</title>
<link rel="stylesheet" href="https://fonts.googleapis.com/css2?family=Mulish:wght@400;600&display=swap">
<style>
  :root {
    --backdrop: #c9cacc;
    --card: #f7f8fa;
    --ink-blue: #2f6fa7;
    --shadow: rgba(0, 0, 0, 0.18);
  }
  * { box-sizing: border-box; margin: 0; padding: 0; }
  html, body {
    width: 1200px; height: 796px; overflow: hidden;
    background: var(--backdrop);
    font-family: "Mulish", sans-serif;
    color: var(--ink-blue);
  }
  .canvas {
    width: 1200px; height: 796px;
    display: flex; align-items: center; justify-content: center; gap: 60px;
  }
  .card {
    position: relative;
    width: 520px; height: 289px;
    background: var(--card);
    box-shadow: 0 6px 18px var(--shadow);
  }
  .firm-name {
    position: absolute;
    font-weight: 600; font-size: 22px; letter-spacing: 0.3px;
  }
  /* back side */
  .card-back .firm-name { top: 42px; left: 44px; }
  .expertise {
    position: absolute; top: 100px; left: 82px;
    font-size: 15px; line-height: 18px;
  }
  .expertise h2 { font-size: 15px; font-weight: 600; }
  .expertise ul { list-style: none; padding-left: 10px; }
  .quote {
    position: absolute; right: 30px; bottom: 28px;
    text-align: right; font-size: 11px; line-height: 15px;
  }
  /* front side */
  .card-front .firm-name { top: 48px; right: 44px; }
  .contact {
    position: absolute; left: 40px; bottom: 34px;
  }
  .contact-name { font-size: 20px; font-weight: 600; margin-bottom: 6px; }
  .contact-list {
    display: grid; grid-template-columns: 56px auto;
    column-gap: 8px; row-gap: 2px; font-size: 14px; line-height: 18px;
  }
  .contact-list dt { font-size: 11px; font-weight: 600; padding-top: 2px; }
  .contact-list .gap { margin-top: 14px; }
</style>
</head>
<body>
<main class="canvas">
  <section class="card card-back" aria-label="Card back">
    <p class="firm-name">Harlow Law</p>
    <div class="expertise">
      <h2>Areas of expertise:</h2>
      <ul>
        <li>property</li>
        <li>commercial</li>
        <li>trusts</li>
        <li>immigration</li>
        <li>franchising</li>
      </ul>
    </div>
    <p class="quote">“Education is when you read the fine print, experience is what you get if you don’t.”<br>Dirk Vanholm</p>
  </section>

  <section class="card card-front" aria-label="Card front">
    <p class="firm-name">Harlow Law</p>
    <div class="contact">
      <p class="contact-name">Glen Harlow</p>
      <dl class="contact-list">
        <dt>Phone</dt><dd>+ 64 9 514 6937</dd>
        <dt>Fax</dt><dd>+ 64 9 514 6936</dd>
        <dt>PO Box</dt><dd>734 Kestrel Bay<br>Tarnhaven 3961 NZ</dd>
        <dt class="gap">email</dt><dd class="gap">glen@fernmarklaw.co.nz</dd>
      </dl>
    </div>
  </section>
</main>
</body>
</html>
```